KRL Stationery Design Project

Dear Designers,
We need a new stationery design for company to match our new logo.
Designers should provide a design for the following:
1. Business Card: 3.5x2 Inches.
2. Letterhead: A4 size.
3. Envelops: 25x35.5 Cm.
You can keep the Arabic name at the bottom of the logo Or you can use the separate attached Arabic Name.
Please refer to the attached logo guide for design information.
Sample Business Card information:
Name: Tarek Sowan
Position: Operation Manager
Tel: +966 920007164 Ex. 500
Fax: +966 (3)8842617
Mob: +966 (5)00263817
email: tarek@krl-example.com.sa
URL: www.krl-example.com.sa
Address:
Nakheel Heights, Suite 718
Zayed bin Omar Str.
Khobar, 31847
Saudi Arabia
Updates
Dear All,
Please note, we had uploaded our logo along with Arabic writing in Adobe illustrator format (.ai).
Regards,
Karim
Dear All,
A sample data for the business card had been added as per your request.
Regards,
Karim

```html
<!DOCTYPE html>
<html lang="en">
<head>
<meta charset="utf-8">
<title>KRL Business Card</title>
<link rel="stylesheet" href="https://fonts.googleapis.com/css2?family=Open+Sans:ital,wght@0,400;0,700;1,700&display=swap">
<style>
  :root {
    --navy: #13294b;
    --grey: #939598;
    --paper: #ffffff;
    --ink: #333333;
    --backdrop: #2a2a2a;
  }
  * { box-sizing: border-box; }
  html, body {
    margin: 0;
    width: 960px;
    height: 1200px;
    overflow: hidden;
    background: var(--backdrop);
    font-family: "Open Sans", Arial, sans-serif;
  }
  .card {
    position: absolute;
    width: 840px;
    height: 478px;
    background: var(--paper);
    border-radius: 30px;
    overflow: hidden;
  }
  .card--front { left: 62px; top: 72px; }
  .card--back  { left: 58px; top: 625px; }

  .brand {
    position: absolute;
    left: 0;
    width: 100%;
    display: flex;
    align-items: center;
    justify-content: center;
    gap: 18px;
    color: var(--navy);
    font-weight: 700;
    font-size: 96px;
    letter-spacing: 2px;
    line-height: 1;
  }
  .card--front .brand { top: 100px; }
  .card--back .brand { top: 170px; }
  .brand__square {
    width: 40px;
    height: 40px;
    background: var(--navy);
  }

  .band {
    position: absolute;
    left: 0;
    top: 316px;
    width: 840px;
    height: 82px;
  }
  .band__grey { fill: var(--grey); }
  .band__navy { fill: var(--navy); }

  .person {
    position: absolute;
    left: 64px;
    top: 328px;
    color: var(--navy);
  }
  .person__name { font-size: 25px; line-height: 30px; margin: 0; font-weight: 400; }
  .person__role { font-size: 19px; line-height: 28px; margin: 0; }

  .address {
    position: absolute;
    right: 36px;
    top: 330px;
    color: var(--paper);
    text-align: right;
    font-size: 19px;
    line-height: 28px;
    margin: 0;
    font-style: normal;
  }

  .contacts {
    position: absolute;
    left: 0;
    top: 408px;
    width: 100%;
    text-align: center;
    color: var(--ink);
    font-size: 19px;
    line-height: 28px;
    margin: 0;
  }
  .contacts b { font-weight: 700; font-style: italic; }
  .contacts .sep { margin: 0 8px; }
</style>
</head>
<body>

<section class="card card--front" aria-label="Business card front">
  <div class="brand"><span class="brand__square"></span><span>KRL</span></div>

  <svg class="band" viewBox="0 0 840 82" aria-hidden="true">
    <polygon class="band__grey" points="0,0 383,0 288,82 0,82"/>
    <polygon class="band__navy" points="400,0 840,0 840,82 306,82"/>
  </svg>

  <div class="person">
    <p class="person__name">Your Name</p>
    <p class="person__role">Designation</p>
  </div>

  <address class="address">1234, Suite# 123<br>Street Name, Country Code</address>

  <p class="contacts">
    <b>t</b> : 123-123-1234<span class="sep">|</span><b>f</b> : 123-123-1234<br>
    <b>e</b> : info@krl-example.com.sa<span class="sep">|</span><b>w</b> : www.krl-example.com.sa
  </p>
</section>

<section class="card card--back" aria-label="Business card back">
  <div class="brand"><span class="brand__square"></span><span>KRL</span></div>
</section>

</body>
</html>
```